Unique Business Card Design

Unique Business Card design for our orthotic and prosthetic company. Our logo is on our website, color is light blue. Unique shape (artificial leg shaped, vertical, etc..) preferred. Logo, business name, individual name and basic demographics needed.

Industry/Entity Type

Business

Contact Information for Business Card

Logo, Industry, Phone # Logo, "Prosthetic & Orthotic Services" Place to add individual name and contact info

Colors
cee9f5

Requirements
Must have
• The icon must be there, placement of "Prosthetic & Orthotic Services" can be moved
Nice to have
• Like the mix of light blue, and a little darker blue. One design included the icons from my website which was a nice touch

```html
<!DOCTYPE html>
<html lang="en">
<head>
<meta charset="utf-8">
<title>LimbWorks Inc. Business Card</title>
<link rel="stylesheet" href="https://fonts.googleapis.com/css2?family=Open+Sans:wght@600&family=Roboto:ital,wght@0,400;0,700;1,400&family=Crimson+Text:ital@1&display=swap">
<style>
  :root {
    --brand-blue: #236397;
    --brand-blue-deep: #1f5a8b;
    --paper: #f6f6f6;
    --ink: #333333;
    --backdrop: #e4e4e4;
    --on-blue: #ffffff;
  }
  * { margin: 0; padding: 0; box-sizing: border-box; }
  html, body { width: 1200px; height: 576px; overflow: hidden; }
  body { background: var(--backdrop); position: relative; font-family: "Roboto", sans-serif; }

  .card { position: absolute; border-radius: 6px; }
  .card--front { left: 82px; top: 139px; width: 484px; height: 291px;
    background: linear-gradient(180deg, var(--brand-blue) 0%, var(--brand-blue-deep) 100%); color: var(--on-blue); }
  .card--back { left: 602px; top: 139px; width: 480px; height: 289px; background: var(--paper); color: var(--ink); }

  .brand-dot { position: absolute; border-radius: 50%; }
  .card--front .brand-dot { left: 91px; top: 107px; width: 78px; height: 78px; background: var(--on-blue); }
  .card--back .brand-dot { left: 85px; top: 79px; width: 86px; height: 86px; background: var(--brand-blue); }

  .brand-name { position: absolute; font-family: "Open Sans", sans-serif; font-weight: 600; white-space: nowrap; letter-spacing: 0.2px; }
  .card--front .brand-name { left: 190px; top: 108px; font-size: 22px; }
  .card--back .brand-name { left: 43px; top: 166px; font-size: 21px; color: var(--brand-blue); }

  .tagline { position: absolute; font-family: "Crimson Text", serif; font-style: italic; white-space: nowrap; }
  .card--front .tagline { left: 203px; top: 142px; font-size: 14px; }
  .card--back .tagline { left: 54px; top: 196px; font-size: 12.5px; color: var(--brand-blue); }

  .front-phone { position: absolute; left: 213px; top: 160px; font-family: "Open Sans", sans-serif; font-weight: 600; font-size: 21px; letter-spacing: 0.6px; }

  .person-name { position: absolute; left: 248px; top: 51px; font-size: 19px; font-weight: 700; color: var(--brand-blue); }
  .person-title { position: absolute; left: 248px; top: 76px; font-size: 12px; font-style: italic; }
  .contact-list { position: absolute; left: 250px; list-style: none; }
  .contact-list--mobile { top: 94px; font-size: 15px; }
  .contact-list--office { top: 142px; font-size: 13px; }
  .contact-list li { display: flex; align-items: center; gap: 9px; height: 17.5px; }
  .contact-list svg { width: 12px; height: 12px; fill: var(--brand-blue); flex: none; }
  .address { position: absolute; left: 248px; top: 218px; font-size: 13px; }
</style>
</head>
<body>
  <section class="card card--front" aria-label="Card front">
    <span class="brand-dot"></span>
    <div class="brand-name">LIMBWORKS INC.</div>
    <div class="tagline">Prosthetic &amp; Orthotic Services</div>
    <div class="front-phone">718.555.0170</div>
  </section>

  <section class="card card--back" aria-label="Card back">
    <span class="brand-dot"></span>
    <div class="brand-name">LIMBWORKS INC.</div>
    <div class="tagline">Prosthetic &amp; Orthotic Services</div>

    <h1 class="person-name">Miriam Kessler</h1>
    <p class="person-title">Orthotist/Prosthetist</p>

    <ul class="contact-list contact-list--mobile">
      <li><svg viewBox="0 0 12 12"><path d="M3 0h6a1 1 0 0 1 1 1v10a1 1 0 0 1-1 1H3a1 1 0 0 1-1-1V1a1 1 0 0 1 1-1zm0 1.5v8h6v-8z"/></svg>845-555-0142</li>
    </ul>

    <ul class="contact-list contact-list--office">
      <li><svg viewBox="0 0 12 12"><path d="M1 4c0-2 2-3 5-3s5 1 5 3v1H8.5V3.8h-5V5H1zM2 6h8l1 5H1z"/></svg>718.555.0170</li>
      <li><svg viewBox="0 0 12 12"><path d="M3 0h6v3H3zM1 4h10v5H9V7H3v2H1zM3.5 8h5v4h-5z"/></svg>718.555.0139</li>
      <li><svg viewBox="0 0 12 12"><path d="M6 0a6 6 0 1 0 0 12A6 6 0 0 0 6 0zm0 1.2c.7 0 1.4 1.6 1.5 4.2h-3C4.6 2.8 5.3 1.2 6 1.2zM1.3 5.4h2.1c0-1.5.3-2.8.7-3.6A4.8 4.8 0 0 0 1.3 5.4zm0 1.2a4.8 4.8 0 0 0 2.8 3.6c-.4-.8-.7-2.1-.7-3.6zm3.2 0h3c-.1 2.6-.8 4.2-1.5 4.2s-1.4-1.6-1.5-4.2zm4.1 0c0 1.5-.3 2.8-.7 3.6a4.8 4.8 0 0 0 2.8-3.6zm2.1-1.2a4.8 4.8 0 0 0-2.8-3.6c.4.8.7 2.1.7 3.6z"/></svg>www.limbworksinc.com</li>
      <li><svg viewBox="0 0 12 12"><path d="M0 2h12v1L6 7 0 3zm0 2.3 6 4 6-4V10H0z"/></svg>Mkessler@limbworksinc.com</li>
    </ul>

    <p class="address">2150 Elm Park Ave. Brooklyn, NY 11229</p>
  </section>
</body>
</html>
```